Business Performance Improvement Book Cover Design Project

We need a book cover design for a new company, based in Eastern Australia, called Brovanta Consulting. We advise clients on process improvement, continuous improvement and business performance improvement, especially in the manufacturing areas and Fast Moving Consumer Goods industries.
We have a written a book designed to demonstrate our very high calibre of knowledge and to use as a marketing tool for prospective clients. We hope to give it out at training seminars and as a comprehensive business card.

Title of the book is: A rounded method for Enterprise Results Advancement.
Subtitle: Shape a Steady Refinement method to fit your firm's character.
Author: by Gareth Polwyn
Back Cover: No need for a bar code in this edition. An important aspect is that we will distribute by hand. Text below for back page.

'For the experienced Business Performers, this book is designed to offer an insight into the advantages and an example of an approach to Business Improvement. It is not the only way but it is tried and tested in world class companies and it works. For those new to Continuous Improvement, it offers a helpful introduction to a holistic business improvement system, an overview of important success factors and pitfalls, recommendations on how to implement tools and methods and a quick guide to see when to use which tools. '

'Consultancies are one of many tools management teams can engage and management must make sure the consultants tailor their approach to suit its business needs and culture and not vice versa.'

End of text for back cover.

Business Performance Improvement is also known as or can include:
Continuous Improvement
Process Improvement
Lean Six Sigma
Operational Excellence
Total Productive Maintenance
Varmeco Output Method
Total Quality Management
Business Process Re engineering
Yield Compass
=
Brovanta Consulting

The book size is 175 x 240 mm and will need a 10-15mm bleed. The spine is not known at this stage exactly and will need to be updated once the printing is finished but I suggest a 10mm until I have the exact size.

Our company colours are Pantone 288, R0,G75,B141, C100,M79,Y17,K3. Attached are some other publications that give a sense of what we like to portray, Some words which might add to this are: professional, elegance, quality, sleek.
Updates

Reason: After receiving the designs, I realised that I needed to update the brief with more and better quality information for designers to work with.

Target Market(s)

people in the accounting and insolvency industries, production managers and CEOs, Chief Operating Officers, members of the executive team of large companies and GMs of small companies.

Industry/Entity Type

Marketing

Requirements
Must have
• Communicate an image that shows an improvement or increase of something.
Very professional and elegant
Emphasis on the words 'Business Performance Improvement' in the title, subtitle also important
Must appeal to a high-end of the market audience
Nice to have
• Recommendation for your cover to be gloss or matt in print
Image can be indirectly related to money but not specifically
Somehow that it matches or is not so different to the attached brochure
Should not have
• Not be too loud or commercial
Book jacket. WIll be printed as soft cover first run and hard cover 2nd run

```html
<!DOCTYPE html>
<html lang="en">
<head>
<meta charset="utf-8">
<title>A Rounded Method For Enterprise Results Advancement — Book Cover</title>
<link rel="stylesheet" href="https://fonts.googleapis.com/css2?family=Comfortaa:wght@500;700&display=swap">
<style>
  :root {
    --cover-blue: #114a8a;
    --paper-white: #ffffff;
    --ornament-lilac: #dfe0ee;
    --type-white: #ffffff;
  }
  html, body {
    margin: 0;
    padding: 0;
    overflow: hidden;
    background: #e9ebef;
  }
  .cover {
    position: relative;
    width: 846px;
    height: 1200px;
    overflow: hidden;
    background: var(--cover-blue);
    font-family: "Comfortaa", "Trebuchet MS", sans-serif;
    color: var(--type-white);
  }
  .cover-art {
    position: absolute;
    inset: 0;
    width: 846px;
    height: 1200px;
  }
  .title {
    position: absolute;
    top: 62px;
    right: 44px;
    margin: 0;
    text-align: right;
    font-weight: 700;
    font-size: 60px;
    line-height: 105px;
    letter-spacing: 0.5px;
  }
  .title span { display: block; }
  .subtitle {
    position: absolute;
    top: 594px;
    right: 44px;
    margin: 0;
    text-align: right;
    font-weight: 700;
    font-size: 27px;
    line-height: 50px;
  }
  .subtitle span { display: block; }
  .author {
    position: absolute;
    left: 236px;
    top: 1138px;
    margin: 0;
    font-weight: 700;
    font-size: 24px;
    letter-spacing: 0.3px;
    white-space: nowrap;
  }
</style>
</head>
<body>
  <main class="cover">
    <svg class="cover-art" viewBox="0 0 846 1200" xmlns="http://www.w3.org/2000/svg">
      <defs>
        <radialGradient id="ornament-glow-top" cx="0.35" cy="0.35" r="0.7">
          <stop offset="0" stop-color="var(--ornament-lilac)" stop-opacity="0.75"/>
          <stop offset="1" stop-color="var(--ornament-lilac)" stop-opacity="0.15"/>
        </radialGradient>
        <radialGradient id="ornament-glow-bottom" cx="0.3" cy="0.6" r="0.7">
          <stop offset="0" stop-color="var(--ornament-lilac)" stop-opacity="0.75"/>
          <stop offset="1" stop-color="var(--ornament-lilac)" stop-opacity="0.15"/>
        </radialGradient>
      </defs>

      <rect class="ornament ornament-top" x="0" y="0" width="370" height="440" rx="60"
            fill="url(#ornament-glow-top)" role="img"
            aria-label="Decorative floral scroll with leaves and a flower, in pale lilac"/>
      <rect class="ornament ornament-bottom" x="0" y="800" width="270" height="400" rx="60"
            fill="url(#ornament-glow-bottom)" role="img"
            aria-label="Decorative leaf and swirl flourish, in pale lilac"/>

      <polygon class="paper-panel" points="0,160 215,450 215,742 0,1010" fill="var(--paper-white)"/>

      <g class="rising-arrow" fill="var(--paper-white)">
        <rect x="237" y="478" width="13" height="230"/>
        <rect x="258" y="508" width="10" height="172"/>
        <rect x="277" y="538" width="8" height="112"/>
        <polygon points="301,572 319,593 301,614"/>
      </g>
    </svg>

    <h1 class="title">
      <span>A Rounded</span>
      <span>Method For</span>
      <span>Enterprise</span>
      <span>Results</span>
      <span>Advancement</span>
    </h1>

    <p class="subtitle">
      <span>Shape a</span>
      <span>Steady Refinement</span>
      <span>method to fit your</span>
      <span>firm's character.</span>
    </p>

    <p class="author">Gareth Polwyn B. Mech Eng., M. Sc (NVT)</p>
  </main>
</body>
</html>
```